Stylish business cards for KV7

To create an appealing and professional business card design for a WOMEN Owned Construction Supply Company.
2 sided card. Incorporate brand elements, curvy, colorful, sleek and bright. No solid white background. attached samples of styles added shapes/ribbons. Want something with that WOW that looks awesome, factor. It is a new logo, so feel free to mess with logo colors in the blue and teal factors that can look good with both dark and light background. If you want to try a watermark with just the KV7, without the "Supply" that might look cool to.

Industry/Entity Type

Women owned construction supply company

Contact Information for Business Card

Name, Title, and phone number and email, web page. maybe spot for qr code.

Font styles to use
Sans Serif

Requirements
Nice to have
• would love to see colors, maybe stylish ribbon dividers or some sort of 2 or 3 tone color card that compliments logo.
Should not have
• Please do not have all white background. Do not include Home/reale state/ or building images.

```html
<!DOCTYPE html>
<html lang="en">
<head>
<meta charset="UTF-8">
<title>KV7 Supply – Business Cards</title>
<link rel="stylesheet" href="https://fonts.googleapis.com/css2?family=Montserrat:wght@500;600;700&display=swap">
<style>
  :root {
    --navy: #142e50;
    --navy-deep: #0f2a4b;
    --teal: #25a3d3;
    --white: #ffffff;
    --backdrop: #3a3a3c;
  }
  * { box-sizing: border-box; margin: 0; padding: 0; }
  html, body {
    width: 1200px; height: 1200px; overflow: hidden;
    background: var(--backdrop);
    font-family: "Montserrat", sans-serif;
  }
  .canvas {
    width: 1200px; height: 1200px;
    display: flex; flex-direction: column; align-items: center; justify-content: center;
    gap: 60px;
  }
  .card {
    position: relative;
    width: 820px; height: 469px;
    border-radius: 38px;
    overflow: hidden;
    border-bottom: 5px solid var(--teal);
    box-shadow: 0 18px 40px rgba(0,0,0,.45);
  }
  .card-bg { position: absolute; inset: 0; width: 100%; height: 100%; }

  /* front */
  .contact-block {
    position: absolute; left: 78px; top: 190px;
    color: var(--white);
    z-index: 1;
  }
  .person-name {
    font-weight: 700; font-size: 40px; color: var(--teal);
    letter-spacing: 1px; line-height: 1;
  }
  .person-title {
    font-weight: 500; font-size: 22px; letter-spacing: 1px;
    margin-top: 8px; margin-bottom: 22px;
  }
  .contact-list { list-style: none; }
  .contact-item {
    display: flex; align-items: center; gap: 14px;
    font-size: 20px; font-weight: 500; letter-spacing: .5px;
    margin-bottom: 12px;
  }
  .contact-icon { width: 24px; height: 24px; flex: none; }

  .brand-name {
    position: absolute;
    font-weight: 700; letter-spacing: 1px; white-space: nowrap;
    line-height: 1;
    z-index: 1;
  }
  .brand-name--front {
    left: 520px; width: 260px; top: 150px;
    text-align: center;
    font-size: 44px; color: var(--navy);
  }
  .brand-name--back  {
    left: 50%; top: 50%; transform: translate(-50%, -50%);
    font-size: 82px; color: var(--white);
  }
  .card--back { background: var(--navy-deep); }
</style>
</head>
<body>
<main class="canvas">

  <section class="card card--front" aria-label="Business card front">
    <svg class="card-bg" viewBox="0 0 820 469" preserveAspectRatio="none" aria-hidden="true">
      <rect width="820" height="469" fill="var(--white)"/>
      <path d="M0 0 H300 C420 0 445 120 470 250 C495 380 555 469 640 469 H0 Z" fill="var(--navy)"/>
      <path d="M318 2 C430 12 458 120 484 245 C508 360 560 450 655 469" fill="none" stroke="var(--teal)" stroke-width="8" stroke-linecap="round"/>
    </svg>

    <div class="contact-block">
      <p class="person-name">FULL NAME</p>
      <p class="person-title">TITLE</p>
      <ul class="contact-list">
        <li class="contact-item">
          <svg class="contact-icon" viewBox="0 0 24 24" aria-hidden="true"><path fill="var(--teal)" d="M6.6 10.8a15 15 0 0 0 6.6 6.6l2.2-2.2c.3-.3.7-.4 1-.2 1.1.4 2.3.6 3.6.6.6 0 1 .4 1 1V20c0 .6-.4 1-1 1A17 17 0 0 1 3 4c0-.6.4-1 1-1h3.5c.6 0 1 .4 1 1 0 1.3.2 2.5.6 3.6.1.3 0 .7-.2 1z"/></svg>
          (000) 000 0000
        </li>
        <li class="contact-item">
          <svg class="contact-icon" viewBox="0 0 24 24" aria-hidden="true"><rect x="2" y="5" width="20" height="14" rx="1" fill="var(--teal)"/><path d="M2 6l10 7 10-7" fill="none" stroke="var(--navy)" stroke-width="1.8"/></svg>
          email@company.com
        </li>
        <li class="contact-item">
          <svg class="contact-icon" viewBox="0 0 24 24" aria-hidden="true"><g fill="none" stroke="var(--teal)" stroke-width="1.8"><circle cx="12" cy="12" r="10"/><ellipse cx="12" cy="12" rx="4.5" ry="10"/><path d="M2 12h20M4 7h16M4 17h16"/></g></svg>
          www.company.com
        </li>
      </ul>
    </div>

    <p class="brand-name brand-name--front">KV7 Supply</p>
  </section>

  <section class="card card--back" aria-label="Business card back">
    <p class="brand-name brand-name--back">KV7 Supply</p>
  </section>

</main>
</body>
</html>
```